KBT Business Cards

We require business cards for our business. We would like a matte black back to the card, with our logo centred in the middle. The front side of the card is open to design.

Target Market(s)

Clients looking for legal services (professional)

Industry/Entity Type

Legal

Contact Information for Business Card

Doran Kelbrath
Partner
Mobile: 0461 738 524
Email: doran@kbtlaw.co
Website: www.kbtlaw.co
Level 3, 118 Wendmore Street
Sydney NSW 2000

Font styles to use
Other font styles liked:
• Avenir

Colors
f04a50
ffffff
1b1b1b

Requirements
Must have
• Black back with logo included in the centre of the card.
• Our font is Avenir.

```html
<!DOCTYPE html>
<html lang="en">
<head>
<meta charset="utf-8">
<title>KBT Business Cards</title>
<link rel="stylesheet" href="https://fonts.googleapis.com/css2?family=Nunito+Sans:wght@300;400;700;800&display=swap">
<style>
  :root {
    --accent: #f04a50;
    --white: #ffffff;
    --card: #1b1b1b;
    --stage: #262626;
    --muted: #8a8a8a;
    --text-soft: #d9d9d9;
  }
  * { box-sizing: border-box; margin: 0; padding: 0; }
  html, body {
    width: 1200px;
    height: 895px;
    overflow: hidden;
    background: var(--stage);
    font-family: "Nunito Sans", "Avenir", sans-serif;
  }
  .stage { position: relative; width: 1200px; height: 895px; }

  .card {
    position: absolute;
    width: 520px;
    height: 300px;
    background: var(--card);
    border-radius: 14px;
    border-bottom: 5px solid var(--accent);
    box-shadow: 0 18px 40px rgba(0,0,0,0.45);
  }
  .card--back { left: 80px; top: 110px; }
  .card--front { left: 600px; top: 480px; }

  .brand {
    display: flex;
    align-items: center;
    gap: 16px;
  }
  .brand__square {
    width: 58px;
    height: 58px;
    background: currentColor;
  }
  .brand__name {
    font-weight: 800;
    font-size: 23px;
    line-height: 1.02;
    letter-spacing: 0.5px;
    text-transform: uppercase;
  }

  .card--back .brand {
    position: absolute;
    left: 50%;
    top: 50%;
    transform: translate(-50%, -50%);
    color: var(--muted);
  }

  .card--front .brand {
    position: absolute;
    left: 34px;
    bottom: 58px;
    color: var(--white);
  }
  .card--front .brand__square { width: 52px; height: 52px; }
  .card--front .brand__name { font-size: 21px; }

  .divider {
    position: absolute;
    left: 272px;
    top: 52px;
    width: 1px;
    height: 190px;
    background: var(--white);
  }

  .details {
    position: absolute;
    left: 296px;
    top: 50px;
    color: var(--text-soft);
    font-weight: 300;
    font-size: 12.5px;
    line-height: 1.45;
  }
  .details__name {
    color: var(--accent);
    font-weight: 800;
    font-size: 20px;
    letter-spacing: 0.6px;
    text-transform: uppercase;
    line-height: 1.1;
  }
  .details__role { font-size: 12.5px; margin-bottom: 16px; }
  .details__address { margin-bottom: 14px; }
  .contact { list-style: none; }
  .contact li { display: flex; align-items: center; gap: 8px; }
  .contact svg { width: 12px; height: 12px; flex: none; }
  .contact .domain { color: var(--accent); }
</style>
</head>
<body>
<main class="stage">

  <section class="card card--back" aria-label="Card back">
    <div class="brand">
      <span class="brand__square" aria-hidden="true"></span>
      <span class="brand__name">Kelbrath<br>Bryce<br>Legal</span>
    </div>
  </section>

  <section class="card card--front" aria-label="Card front">
    <div class="brand">
      <span class="brand__square" aria-hidden="true"></span>
      <span class="brand__name">Kelbrath<br>Bryce<br>Legal</span>
    </div>

    <span class="divider" aria-hidden="true"></span>

    <div class="details">
      <p class="details__name">Doran Kelbrath</p>
      <p class="details__role">Partner</p>
      <p class="details__address">Level 3, 118 Wendmore Street<br>Sydney NSW 2000</p>
      <ul class="contact">
        <li>
          <svg viewBox="0 0 12 12" aria-hidden="true"><rect x="3" y="0.8" width="6" height="10.4" rx="1" fill="none" stroke="#f04a50" stroke-width="1.2"/><line x1="5" y1="9.3" x2="7" y2="9.3" stroke="#f04a50" stroke-width="1"/></svg>
          0461 738 524
        </li>
        <li>
          <svg viewBox="0 0 12 12" aria-hidden="true"><rect x="0.8" y="2.5" width="10.4" height="7" fill="none" stroke="#f04a50" stroke-width="1.2"/><polyline points="1,3 6,7 11,3" fill="none" stroke="#f04a50" stroke-width="1.2"/></svg>
          <span>doran@<span class="domain">kbtlaw</span>.co</span>
        </li>
        <li>
          <svg viewBox="0 0 12 12" aria-hidden="true"><path d="M6 11 C3 7.5 2 6 2 4.5 A4 4 0 0 1 10 4.5 C10 6 9 7.5 6 11 Z" fill="none" stroke="#f04a50" stroke-width="1.2"/><circle cx="6" cy="4.6" r="1.3" fill="#f04a50"/></svg>
          <span>www.<span class="domain">kbtlaw</span>.co</span>
        </li>
      </ul>
    </div>
  </section>

</main>
</body>
</html>
```